Redesign of business card for Cedar Ridge Mechanical

We are looking for a new design for our business cards for Cedar Ridge Mechanical. We are a plumbing & HVAC construction company, operating on the West Coast of Canada and USA. Logo attached.
Industry/Entity Type
Construction - Plumbing & HVAC
Contact Information for Business Card
Name, address, phone numbers, email, website address
Look and feel
Each slider illustrates characteristics of the customer's brand and the style your logo design should communicate.

```html
<!DOCTYPE html>
<html lang="en">
<head>
<meta charset="utf-8">
<title>Cedar Ridge Mechanical — Business Card</title>
<link href="https://fonts.googleapis.com/css2?family=Montserrat:wght@400;500;700&display=swap" rel="stylesheet">
<style>
  :root {
    --bg: #1a1a1a;
    --card: #151515;
    --ink: #ffffff;
    --band-light: #e6e6e6;
    --band-dark: #8a8a8a;
  }
  * { margin: 0; padding: 0; box-sizing: border-box; }
  html, body { width: 1200px; height: 963px; overflow: hidden; }
  body {
    background: var(--bg);
    font-family: "Montserrat", sans-serif;
    color: var(--ink);
    position: relative;
  }
  .card {
    position: absolute;
    left: 250px;
    width: 700px;
    height: 400px;
    background: var(--card);
    border-radius: 22px;
    overflow: hidden;
    box-shadow: 0 10px 30px rgba(0,0,0,.5);
  }
  .card--front { top: 60px; }
  .card--back { top: 503px; }

  .brand-name {
    font-family: "Montserrat", sans-serif;
    font-weight: 700;
    text-transform: uppercase;
    color: var(--ink);
    line-height: 1.15;
    white-space: nowrap;
  }
  .front-brand {
    position: absolute;
    left: 50px;
    top: 120px;
    display: flex;
    align-items: center;
    gap: 16px;
  }
  .front-brand .brand-mark {
    width: 38px; height: 38px; flex: none;
    border: 5px solid var(--ink);
    border-radius: 6px;
  }
  .front-brand .brand-name { font-size: 24px; letter-spacing: 1px; }

  .divider {
    position: absolute;
    left: 345px; top: 50px;
    width: 1px; height: 250px;
    background: var(--ink);
  }
  .contact {
    position: absolute;
    left: 380px; top: 58px;
    width: 300px;
  }
  .contact__name { font-size: 26px; font-weight: 700; text-transform: uppercase; letter-spacing: .5px; white-space: nowrap; }
  .contact__role { font-size: 18px; font-weight: 400; margin-bottom: 16px; }
  .contact__address { font-size: 19px; line-height: 1.2; margin-bottom: 12px; }
  .contact__row { display: flex; align-items: center; gap: 9px; font-size: 17px; line-height: 1.45; white-space: nowrap; }
  .contact__row svg { width: 14px; height: 14px; flex: none; fill: var(--ink); }

  .band {
    position: absolute;
    left: 0; bottom: 40px;
    width: 100%; height: 34px;
    background: linear-gradient(90deg, var(--band-light) 0%, #bdbdbd 60%, var(--band-dark) 100%);
  }
  .band__mark {
    position: absolute;
    right: 90px; bottom: 36px;
    width: 42px; height: 42px;
    background: var(--card);
    border: 4px solid var(--ink);
    border-radius: 6px;
  }

  .back-pattern {
    position: absolute; inset: 0;
    background: radial-gradient(circle at 50% 50%, #1d1d1d, #121212);
  }
  .back-brand {
    position: absolute;
    left: 50%; top: 50%;
    transform: translate(-50%, -50%);
    display: flex; align-items: center; gap: 24px;
  }
  .back-brand .brand-mark {
    width: 64px; height: 64px; flex: none;
    border: 8px solid var(--ink);
    border-radius: 10px;
  }
  .back-brand .brand-name { font-size: 40px; letter-spacing: 2px; }
</style>
</head>
<body>
  <section class="card card--front" aria-label="Business card front">
    <div class="front-brand">
      <span class="brand-mark"></span>
      <span class="brand-name">Cedar Ridge<br>Mechanical</span>
    </div>
    <div class="divider"></div>
    <div class="contact">
      <p class="contact__name">Daniel Harper</p>
      <p class="contact__role">Manager</p>
      <p class="contact__address">Your address, city<br>state, ZIP 0000</p>
      <p class="contact__row">
        <svg viewBox="0 0 24 24"><path d="M6.6 10.8a15.1 15.1 0 0 0 6.6 6.6l2.2-2.2c.3-.3.7-.4 1-.2 1.1.4 2.3.6 3.6.6.6 0 1 .4 1 1V20c0 .6-.4 1-1 1A17 17 0 0 1 3 4c0-.6.4-1 1-1h3.5c.6 0 1 .4 1 1 0 1.3.2 2.5.6 3.6.1.3 0 .7-.2 1z"/></svg>
        123-456-2100
      </p>
      <p class="contact__row">
        <svg viewBox="0 0 24 24"><path d="M2 5h20v14H2zM4 7v.5l8 5 8-5V7zm0 2.8V17h16V9.8l-8 5z"/></svg>
        contact@cedarridgemech.com
      </p>
      <p class="contact__row">
        <svg viewBox="0 0 24 24"><path d="M12 2a10 10 0 1 0 0 20 10 10 0 0 0 0-20zm6.9 6h-2.9a15.6 15.6 0 0 0-1.4-3.6A8 8 0 0 1 18.9 8zM12 4c.8 1.2 1.5 2.5 1.9 4h-3.8c.4-1.5 1.1-2.8 1.9-4zM4.3 14a8 8 0 0 1 0-4h3.4a16 16 0 0 0 0 4zm.8 2h2.9c.3 1.3.8 2.5 1.4 3.6A8 8 0 0 1 5.1 16zM8 8H5.1a8 8 0 0 1 4.3-3.6C8.8 5.5 8.3 6.7 8 8zm4 12c-.8-1.2-1.5-2.5-1.9-4h3.8c-.4 1.5-1.1 2.8-1.9 4zm2.3-6H9.7a14.7 14.7 0 0 1 0-4h4.6a14.7 14.7 0 0 1 0 4zm.3 5.6c.6-1.1 1.1-2.3 1.4-3.6h2.9a8 8 0 0 1-4.3 3.6zm1.7-5.6a16 16 0 0 0 0-4h3.4a8 8 0 0 1 0 4z"/></svg>
        www.cedarridgemech.com
      </p>
    </div>
    <div class="band"></div>
    <span class="band__mark"></span>
  </section>

  <section class="card card--back" aria-label="Business card back">
    <div class="back-pattern" role="img" aria-label="Faint repeating embossed brand pattern"></div>
    <div class="back-brand">
      <span class="brand-mark"></span>
      <span class="brand-name">Cedar Ridge<br>Mechanical</span>
    </div>
  </section>
</body>
</html>
```